Commercial Real Estate Corporate Site

Our company sells an ERP software to Commercial Real Estate Companies, this project is part of a marketing and sales relaunch of the company.

See attached for PDF formatted Design brief

The software is a modular system where client’s can adopt one module at a time. Our customers are corporate clients who own between 10M and 10B of real estate properties. The typical customer is from the IT or the Financial arm of the company. Our differentiation in the market is that our system is built on a no-code environment, so making changes for the client is quick. Incumbents in the market have long implementation cycles, and customization is often not possible. Competitors are Quorvel, TKB, PlotNest, Vumora.

We need a design for our site which will be implemented into Brevo Forge. **All designs must be compatible with the newest version of Brevo Forge.**

We have produced the following attached assets to use in the website design.:

1. Logo
2. Brand Guidelines
3. Content for Pages
4. Menu Structures
5. Illustrations (modules)
I can't attach them because the files are too big, so they're in this google drive instead:
https://files.examplestore.net/share/k29Xa7Lq0Pz3Rt8MwB5nYc4Hv1Jd6Fe?mode=view

The mechanic for our sales process is as follows:

1. We find on module from our application that a client is interested in. The illustrations that we’ve attached represent the individual modules (elements) of the software.
1. For instance, one of our current customers has purchased a commissions module from us which helps calculate the commission that brokers receive for buying and selling their properties.
2. We provide immense value through the module, and then keep in sales communication with the client to determine which other modules we can implement for them.
1. For instance, in the example above, the client is so happy with the commissions module that they want to start working with our leasing module as well. In the next business quarter, they also choose to add our financials module to their business systems.

### Logo

Attached

### Brand Guidelines

Attached

We are open to suggestions on the secondary colour palette.

### **Site Copy**

**We require the following pages to be created; For now, we will do one Market Page, one Product Page, and one Platform / Services Page, and we will use those as inspiration to create the other dozen Marketing Pages and 30 or so Product Pages.**

**Homepage**

Attached

**Market Page** - look at the quorvel site under the Office, Industrial, Retail (https://www.quorvel.com/products/quorvel-commercial-suite/)

**Product** - One product provided, but there will be 30 - look at the vumora page

(https://www.vumora.com/products/general-accounting)

**Platform / Services Page** - pages that tell the story of our platform and services, content to be provided - the platform will use our modules as it highlights the story of the configurability and composability of the platform. Instead of the icons that they use, we want to use our modules.

- https://www.pelbrix.com/enterprise-applications-platform
- https://www.pelbrix.com/cloud-architecture

**Team Page** - just add sample content for starters (6 Team Members to start)

**Schedule Demo Page** - the call to action for all pages

(https://go.vumora.com/schedule-demo.html)

### Menu Structure

The menu is provided as an attachment.

### Illustrations Information

A note about the illustrations - we have provided an illustrator file with the modules, and if you’d like you can arrange the in any way that you’d like to. We especially like when the modules are positioned like a periodic table of the elements.

Our existing clients are

- Torvane Coop - https://www.torvanecoop.com/real-estate/
- Dalsworth Realestate https://dalsworth.com

Our competitors are

- Quorvel - www.quorvel.com
- TKB - [www.tkbsoftware.com](https://www.tkbsoftware.com/) (we don’t like how this one looks)
- Vumora - www.vumora.com
- Plotnest - www.plotnest.com

Design inspiration

- https://lark-studio.brevosite.com/velmo
- Corporate
- Established
- Modern

### Stock Images Guidance

- https://www.drafta.net/design/QXR7Lm2TpWz/Hk9vN3c8Yd41-FbqsaZRr/edit?utm_content=QXR7Lm2TpWz&utm_campaign=designshare&utm_medium=link2&utm_source=sharebutton

Target Market(s)

Commercial Real Estate Companies - they typically own a portfolio of 50 - 5000 real estate properties and need a software to manage it all.

Coding

Coded - Design and coding required

Number of Pages Required

5+ page

Font styles to use
Other font styles liked:
• Fonts defined in brand guideline

Requirements
Must have
• Brevo Forge, Use the Elemental Design, Download ai.zip and png.zip Use Brand Guideline,
Nice to have
• Check design breif

```html
<!DOCTYPE html>
<html lang="en">
<head>
<meta charset="UTF-8">
<title>Veltrim – Landing Page Mobile View</title>
<link rel="stylesheet" href="https://fonts.googleapis.com/css2?family=Poppins:wght@400;500;600;700;800&display=swap">
<style>
  :root {
    --red: #e3262b;
    --red-soft: #fde9e9;
    --ink: #16161a;
    --grey: #7a7b82;
    --line: #e6e6ea;
    --board: #f5f5f7;
    --white: #ffffff;
    --photo-a: #5d6f86;
    --photo-b: #b9c4cf;
  }
  * { box-sizing: border-box; margin: 0; padding: 0; }
  html, body { width: 835px; height: 1200px; overflow: hidden; }
  body { background: var(--board); font-family: "Poppins", sans-serif; color: var(--ink); position: relative; }

  .brand { position: absolute; left: 100px; top: 190px; display: flex; align-items: center; gap: 12px; }
  .brand-mark { width: 26px; height: 26px; border-radius: 50%; background: var(--ink); }
  .brand-name { font-size: 30px; font-weight: 600; color: var(--ink); line-height: 1; }

  .board-title { position: absolute; left: 100px; top: 320px; font-size: 40px; line-height: 1.22; font-weight: 700; color: var(--red); }

  .screen { position: absolute; background: var(--white); border-radius: 18px; overflow: hidden; box-shadow: 0 6px 24px rgba(0,0,0,.08); }
  .screen-home { left: 110px; top: 690px; width: 172px; height: 450px; background: linear-gradient(180deg, #eef0f3 0%, #ffffff 60%); padding: 14px 12px; }
  .screen-about { left: 300px; top: 660px; width: 172px; height: 470px; padding: 12px; }

  .topbar { display: flex; justify-content: space-between; align-items: center; margin-bottom: 18px; }
  .topbar-name { font-size: 9px; font-weight: 700; color: var(--red); }
  .burger { width: 12px; height: 8px; border-top: 2px solid var(--ink); border-bottom: 2px solid var(--ink); }

  .hero-heading { font-size: 15px; line-height: 1.25; font-weight: 700; margin-bottom: 8px; }
  .hero-heading em, .section-heading em { font-style: normal; color: var(--red); }
  .body-small { font-size: 6px; line-height: 1.5; color: var(--grey); }
  .buttons { display: flex; gap: 6px; margin: 10px 0 14px; }
  .btn { font-size: 6px; font-weight: 600; padding: 5px 10px; border-radius: 20px; border: 1px solid var(--red); color: var(--red); background: var(--white); }
  .btn-solid { background: var(--red); color: var(--white); }

  .stat-card { background: var(--white); border-radius: 12px; box-shadow: 0 3px 12px rgba(0,0,0,.08); padding: 8px 10px; display: flex; align-items: center; gap: 8px; margin-bottom: 10px; }
  .avatars { display: flex; }
  .avatars span { width: 14px; height: 14px; border-radius: 50%; background: #9aa3ad; border: 2px solid var(--white); margin-left: -5px; }
  .avatars span:first-child { margin-left: 0; background: #6c757f; }
  .stat-icon { width: 18px; height: 18px; border-radius: 50%; background: var(--red-soft); display: grid; place-items: center; flex-shrink: 0; }
  .stat-text { font-size: 7px; font-weight: 600; line-height: 1.3; }

  .photo { background: linear-gradient(160deg, var(--photo-a), var(--photo-b)); border-radius: 8px; }
  .eyebrow { font-size: 5.5px; font-weight: 600; color: var(--red); text-transform: uppercase; letter-spacing: .5px; margin: 10px 0 3px; }
  .section-heading { font-size: 9px; font-weight: 700; line-height: 1.3; margin-bottom: 6px; }
  .feature-card { border: 1px solid var(--line); border-radius: 10px; padding: 8px; margin-bottom: 8px; display: flex; gap: 7px; align-items: flex-start; }
  .feature-title { font-size: 6.5px; font-weight: 600; color: var(--red); margin-bottom: 2px; }

  .strip { position: absolute; background: var(--white); overflow: hidden; }
  .strip-top { left: 593px; top: 0; width: 207px; height: 265px; padding: 14px 16px; }
  .strip-about { left: 593px; top: 285px; width: 207px; height: 472px; padding: 14px 16px; }
  .strip-erp { left: 593px; top: 815px; width: 222px; height: 385px; padding: 16px 16px; background: #fafafb; }

  .strip .body-small { font-size: 7px; }
  .strip .btn { font-size: 7px; }
  .strip .stat-text { font-size: 9px; }
  .strip .section-heading { font-size: 12px; }
  .strip .feature-title { font-size: 8.5px; }
  .strip .eyebrow { font-size: 6.5px; }
  .footnote { font-size: 6px; color: var(--grey); margin-top: 10px; }

  .partners { display: flex; justify-content: space-between; align-items: center; margin-bottom: 12px; }
  .partner-name { font-size: 13px; font-weight: 600; color: #3a3b40; }
  .partner-dot { width: 8px; height: 8px; border-radius: 50%; background: #9a9ba0; }
  .photo-grid { display: grid; grid-template-columns: 1fr 1fr; grid-template-rows: 60px 60px; gap: 6px; height: 126px; }
  .photo-grid .tall { grid-row: span 2; }

  .erp-heading { font-size: 13px; font-weight: 700; line-height: 1.3; margin-bottom: 3px; }
  .erp-heading em { font-style: normal; color: var(--red); }
  .big-number { font-size: 15px; font-weight: 700; margin: 10px 0 2px; }
  .erp-photo { height: 120px; margin-top: 10px; border-radius: 10px; background: linear-gradient(160deg, #3f6fa6, #c9d6e4); }
  .op-item { display: flex; gap: 8px; align-items: flex-start; margin-top: 12px; }
  .op-title { font-size: 10px; font-weight: 700; }
</style>
</head>
<body>

  <div class="brand">
    <span class="brand-mark"></span>
    <span class="brand-name">Veltrim</span>
  </div>

  <h1 class="board-title">Landing Page<br>Mobile View</h1>

  <section class="screen screen-home">
    <div class="topbar"><span class="topbar-name">Veltrim</span><span class="burger"></span></div>
    <h2 class="hero-heading">Revolutionizing<br><em>CRE Management</em><br>Solutions</h2>
    <p class="body-small">One modular platform to run leasing, commissions and financials for your full portfolio.</p>
    <div class="buttons"><span class="btn">Learn More</span><span class="btn btn-solid">Start Now</span></div>
    <div class="stat-card">
      <div class="avatars"><span></span><span></span><span></span></div>
      <div class="stat-text">75k+ Happy<br>Customers</div>
    </div>
    <div class="stat-card">
      <div class="stat-icon"><svg width="9" height="9" viewBox="0 0 10 10"><path d="M1 9V4l4-3 4 3v5z" fill="none" stroke="#e3262b" stroke-width="1.3"/></svg></div>
      <div class="stat-text">200+ New<br>Listings Everyday!</div>
    </div>
  </section>

  <section class="screen screen-about">
    <div class="photo" style="height:120px" role="img" aria-label="Modern glass office towers seen from below"></div>
    <p class="eyebrow">Who we are</p>
    <h3 class="section-heading">Assisting Individuals in locating the appropriate real estate.</h3>
    <div class="feature-card">
      <div class="stat-icon"><svg width="9" height="9" viewBox="0 0 10 10"><circle cx="5" cy="5" r="3.5" fill="none" stroke="#e3262b" stroke-width="1.3"/></svg></div>
      <div><p class="feature-title">Green portfolio matured</p><p class="body-small">Track every asset with clear reports.</p></div>
    </div>
    <div class="feature-card">
      <div class="stat-icon"><svg width="9" height="9" viewBox="0 0 10 10"><path d="M5 1v8M1 5h8" stroke="#e3262b" stroke-width="1.3"/></svg></div>
      <div><p class="feature-title">Green portfolio matured</p><p class="body-small">Add modules one at a time.</p></div>
    </div>
    <h3 class="section-heading" style="margin-top:10px">Get Easier To Build <em>ERP Software</em></h3>
    <p class="body-small">Configure workflows fast with no-code tools.</p>
  </section>

  <section class="strip strip-top">
    <p class="body-small">Simplifies the operations of commercial real estate management solution teams.</p>
    <div class="buttons"><span class="btn">Learn More</span><span class="btn btn-solid">Start Now</span></div>
    <div class="stat-card">
      <div class="avatars"><span></span><span></span><span></span><span></span></div>
      <div class="stat-text">75k+ Happy<br>Customers</div>
    </div>
    <div class="stat-card">
      <div class="stat-icon"><svg width="10" height="10" viewBox="0 0 10 10"><path d="M1 9V4l4-3 4 3v5z" fill="none" stroke="#e3262b" stroke-width="1.3"/></svg></div>
      <div class="stat-text">200+ New<br>Listings Everyday!</div>
    </div>
    <p class="footnote">Crafted by Veltrim. Compliance across the globe.</p>
  </section>

  <section class="strip strip-about">
    <div class="partners">
      <span class="partner-name">halden</span>
      <span class="partner-name">norvik</span>
      <span class="partner-dot"></span>
    </div>
    <div class="photo-grid">
      <div class="photo tall" role="img" aria-label="Curved glass building facade"></div>
      <div class="photo" role="img" aria-label="Office tower exterior"></div>
      <div class="photo" role="img" aria-label="Modern lobby interior"></div>
    </div>
    <p class="eyebrow">Who we are</p>
    <h3 class="section-heading">Assisting Individuals in locating the appropriate real estate.</h3>
    <p class="body-small" style="margin-bottom:12px">Our platform helps owners manage leases, tenants and finances in one place.</p>
    <div class="feature-card">
      <div class="stat-icon"><svg width="10" height="10" viewBox="0 0 10 10"><circle cx="5" cy="5" r="3.5" fill="none" stroke="#e3262b" stroke-width="1.3"/></svg></div>
      <div><p class="feature-title">Green portfolio matured</p><p class="body-small">Sustain growth with clear, real-time asset reporting.</p></div>
    </div>
    <div class="feature-card">
      <div class="stat-icon"><svg width="10" height="10" viewBox="0 0 10 10"><path d="M5 1v8M1 5h8" stroke="#e3262b" stroke-width="1.3"/></svg></div>
      <div><p class="feature-title">Green portfolio matured</p><p class="body-small">Scale by adding new modules each quarter.</p></div>
    </div>
  </section>

  <section class="strip strip-erp">
    <h3 class="erp-heading">Get Easier To Build <em>ERP Software</em></h3>
    <p class="body-small">We help you build a system for your real estate company.</p>
    <p class="big-number">40,000 ++</p>
    <p class="body-small">Properties managed on our platform</p>
    <div class="erp-photo" role="img" aria-label="Blue glass skyscraper with sweeping curves"></div>
    <div class="op-item">
      <div class="stat-icon"><svg width="10" height="10" viewBox="0 0 10 10"><path d="M2 5l2 2 4-4" fill="none" stroke="#e3262b" stroke-width="1.4"/></svg></div>
      <div><p class="op-title">Streamlined Operations</p><p class="body-small">Optimize workflows and enhance efficiency with tailored modules.</p></div>
    </div>
    <div class="op-item">
      <div class="stat-icon"><svg width="10" height="10" viewBox="0 0 10 10"><path d="M2 8V5M5 8V2M8 8V4" stroke="#e3262b" stroke-width="1.4"/></svg></div>
      <div><p class="op-title">Data-Driven Insights</p><p class="body-small">Make confident decisions with live portfolio data.</p></div>
    </div>
  </section>

</body>
</html>
```